****Business Card Design for Quarrystone Development. Design based around attached logo/company name

I’m looking for business card design for my company Quarrystone Development Group,LLC. Design should be professional, sharp and minimal. Outside of the attached logos, greyscale colors for remainder of cards. My thoughts are two-sided card with attached logo on one side and my info on the other but open to one-sided as well with right design.
Target Market(s)
Real estate professionals including banks, private investors, property owners, developers, commercial tenants like Brewlantern, Grovika or Tanquist’s.
Industry/Entity Type
Commercial real estate development and investments.
Contact Information for Business Card
Name, title, email, phone #’s, web address and physical address
Font styles to use
Other font styles liked:
- Helvetica, Garamond, etc
Colors
Designer to choose only greyscale colors for use in the design.
Requirements
Must have
- Attached logo first or second options.
Nice to have
- Two sided card with logo on one side. Attached Logo/company name can be laid out any way that flows as long as it’s legible.name
Should not have
- No loud colors. ***Please do not include logo, I have removed the company design with a logo image.

```html
<!DOCTYPE html>
<html lang="en">
<head>
<meta charset="UTF-8">
<title>Quarrystone Development Group, LLC — Business Card</title>
<link href="https://fonts.googleapis.com/css2?family=Cinzel:wght@400;700&family=Arimo:wght@400&display=swap" rel="stylesheet">
<style>
  :root {
    --backdrop: #1a1a1a;
    --card: #3a3a3b;
    --ink: #f2f2f2;
    --ink-soft: #c9c9cb;
    --mark-grey: #9a9ca3;
    --rule: #8d8d90;
  }
  * { margin: 0; padding: 0; box-sizing: border-box; }
  html, body { width: 1200px; height: 852px; overflow: hidden; background: var(--backdrop); }
  .canvas { position: relative; width: 1200px; height: 852px; }

  .card {
    position: absolute;
    width: 520px; height: 297px;
    background: var(--card);
    box-shadow: 0 10px 30px rgba(0,0,0,.55);
  }
  .card--front { left: 80px; top: 110px; }
  .card--back  { left: 600px; top: 440px; }

  /* Front: company name */
  .brand {
    position: absolute; left: 0; right: 0; top: 50%;
    transform: translateY(-50%);
    display: flex; align-items: center; justify-content: center; gap: 14px;
  }
  .brand__dot { width: 14px; height: 14px; border-radius: 50%; background: var(--mark-grey); }
  .brand__name {
    font-family: "Cinzel", serif; font-weight: 400; color: var(--ink-soft);
    line-height: 1.15; text-align: left;
  }
  .brand__name .line1 { display: block; font-size: 38px; letter-spacing: 1px; }
  .brand__name .line2 { display: block; font-size: 14.5px; letter-spacing: 1.6px; }

  /* Back: details */
  .person { position: absolute; left: 44px; top: 118px; }
  .person__name {
    font-family: "Cinzel", serif; font-weight: 700; font-size: 19px;
    color: var(--ink); letter-spacing: 1px;
  }
  .person__title { font-family: "Arimo", sans-serif; font-size: 13px; color: var(--ink-soft); margin-top: 4px; margin-left: 14px; }

  .address {
    position: absolute; right: 30px; top: 26px;
    padding-right: 12px; border-right: 1px solid var(--rule);
    font-family: "Arimo", sans-serif; font-size: 13px; line-height: 1.4;
    color: var(--ink-soft); text-align: right;
  }

  .contact {
    position: absolute; left: 44px; bottom: 30px;
    display: flex; gap: 10px; align-items: stretch;
  }
  .contact__icons { display: flex; flex-direction: column; justify-content: space-around; gap: 5px; }
  .contact__icons svg { width: 12px; height: 12px; fill: var(--ink-soft); }
  .contact__list {
    list-style: none; border-left: 1px solid var(--rule); padding-left: 10px;
    font-family: "Arimo", sans-serif; font-size: 14px; line-height: 1.35; color: var(--ink);
  }

  .back-brand {
    position: absolute; right: 28px; bottom: 80px;
    font-family: "Cinzel", serif; font-weight: 400; color: var(--ink-soft); text-align: right;
    line-height: 1.15;
  }
  .back-brand .line1 { display: block; font-size: 25px; letter-spacing: .8px; }
  .back-brand .line2 { display: block; font-size: 9.6px; letter-spacing: 1.2px; }
</style>
</head>
<body>
<main class="canvas">
  <section class="card card--front" aria-label="Card front">
    <div class="brand">
      <span class="brand__dot"></span>
      <p class="brand__name">
        <span class="line1">QUARRYSTONE</span>
        <span class="line2">DEVELOPMENT GROUP, LLC</span>
      </p>
    </div>
  </section>

  <section class="card card--back" aria-label="Card back">
    <address class="address">4172 Marlow<br>Ridge Corvallis, OR 97330</address>

    <div class="person">
      <p class="person__name">DANIEL WHITCOMB</p>
      <p class="person__title">Director</p>
    </div>

    <p class="back-brand">
      <span class="line1">QUARRYSTONE</span>
      <span class="line2">DEVELOPMENT GROUP, LLC</span>
    </p>

    <div class="contact">
      <div class="contact__icons">
        <svg viewBox="0 0 24 24" aria-label="Phone"><path d="M6.6 10.8a15 15 0 0 0 6.6 6.6l2.2-2.2a1 1 0 0 1 1-.25 11.4 11.4 0 0 0 3.6.57 1 1 0 0 1 1 1V20a1 1 0 0 1-1 1A17 17 0 0 1 3 4a1 1 0 0 1 1-1h3.5a1 1 0 0 1 1 1c0 1.25.2 2.45.57 3.57a1 1 0 0 1-.25 1z"/></svg>
        <svg viewBox="0 0 24 24" aria-label="Email"><path d="M2 5h20v14H2zm2 2v.5l8 5 8-5V7zm0 2.9V17h16V9.9l-8 5z"/></svg>
        <svg viewBox="0 0 24 24" aria-label="Website"><circle cx="12" cy="12" r="10"/></svg>
      </div>
      <ul class="contact__list">
        <li>(555) 014-2290</li>
        <li>info@quarrystonegroup.com</li>
        <li>www.quarrystonegroup.com</li>
      </ul>
    </div>
  </section>
</main>
</body>
</html>
```